Company Business Card (Company Promotions)

We want a Business Card that is both Elegant & High Class. We want the card stock thick and unique. We want it to build our Brand Name. We service Automobile dealerships & owners who drive luxury & exotic automobiles that cost an average of $75K. We provide towing services for Luxury & Exotic vehicles. Our colors are Black & Construction Yellow (Gold).
We are manufacture certified for Valdora Kent, RQT, PUKA, ELVO, Tavrine, HJ, Colvesi, Pendrel, Casteduvro, Ombra & Sorvanel. We have authorization to use their logo's.
Enclosed is our old business card. We only used the unusual & Unique brands on the cards but are open to the use of all of them. We also use the Federal Competence Badge that identifies our abilities.

Also enclosed is the name font that we use.

Target Market(s)

Business, Executive, Hi end people that drive finer luxury &/or exotic automobiles.

Industry/Entity Type

Business

Contact Information for Business Card

We market our name. Haul Crestmark. Business address is: 4812 Willowmere Lane, NE Ste: 210, Atlanta, GA 30399 Phone: 404-555-0148. Web address is crestmarkhaul-example.com
Manufacture Certified / Nationally Certified

Font styles to use
Other font styles liked:
• AR DESTINE (in Italic's)

Colors
ffc214

Requirements
Must have
• Must have the at least 5 of the manufacture logo's and the Guild Council Emblem (see on other business card)
Nice to have
• Place the manfacture logo's on the back.
Should not have
• No other colors than Black, Yellow & White

```html
<!DOCTYPE html>
<html lang="en">
<head>
<meta charset="utf-8">
<title>Haul Crestmark – Business Card</title>
<link rel="stylesheet" href="https://fonts.googleapis.com/css2?family=Audiowide&family=Arimo:wght@400;700&display=swap">
<style>
  :root {
    --ink: #0b0b0b;
    --ink-soft: #1c1c1c;
    --gold: #ffc214;
    --white: #ffffff;
    --paper: #ebe8e2;
  }
  * { margin: 0; padding: 0; box-sizing: border-box; }
  html, body { width: 1200px; height: 892px; overflow: hidden; }
  body { background: var(--paper); position: relative; }

  .card {
    position: absolute;
    left: 280px;
    width: 640px;
    height: 366px;
    background: linear-gradient(160deg, var(--ink-soft) 0%, var(--ink) 60%);
    overflow: hidden;
    box-shadow: 0 6px 18px rgba(0,0,0,0.25);
  }
  .card--contact { top: 50px; }
  .card--brand { top: 476px; }

  .brand-first, .brand-main {
    position: absolute;
    font-family: "Audiowide", sans-serif;
    color: var(--gold);
    line-height: 1;
    white-space: nowrap;
  }
  .brand-rule {
    position: absolute;
    height: 3px;
    background: var(--gold);
  }
  .tagline {
    position: absolute;
    font-family: "Audiowide", sans-serif;
    color: var(--white);
    white-space: nowrap;
    letter-spacing: 0.5px;
  }

  /* contact side */
  .card--contact .brand-first { left: 150px; top: 30px; font-size: 38px; }
  .card--contact .brand-main { left: 110px; top: 76px; font-size: 46px; }
  .card--contact .brand-rule { left: 100px; top: 132px; width: 340px; }
  .card--contact .tagline { left: 100px; top: 142px; font-size: 11px; }

  .contact {
    position: absolute;
    left: 40px;
    font-family: "Arimo", sans-serif;
    color: var(--gold);
    white-space: nowrap;
  }
  .contact--phone { top: 196px; font-size: 27px; }
  .contact--web { top: 234px; font-size: 21px; }
  .contact--address { top: 292px; font-size: 15px; }

  .badge { position: absolute; left: 458px; top: 104px; width: 66px; height: 78px; }

  .maker-strip {
    position: absolute;
    right: 0; top: 0;
    width: 96px; height: 100%;
    background: var(--white);
    display: flex;
    flex-direction: column;
    justify-content: space-around;
    align-items: center;
    padding: 8px 0;
  }
  .maker {
    display: flex;
    align-items: center;
    gap: 4px;
    font-family: "Arimo", sans-serif;
    font-weight: 700;
    font-size: 10px;
    color: var(--ink);
    white-space: nowrap;
  }
  .maker-dot {
    width: 8px; height: 8px;
    border-radius: 50%;
    background: var(--ink);
  }

  /* brand side */
  .brand-band {
    position: absolute;
    left: 0; top: 0;
    width: 108px; height: 100%;
    background: var(--gold);
  }
  .card--brand .brand-first { left: 180px; top: 100px; font-size: 46px; }
  .card--brand .brand-main { left: 232px; top: 154px; font-size: 50px; }
  .card--brand .brand-rule { left: 176px; top: 218px; width: 440px; }
  .card--brand .tagline { left: 176px; top: 230px; font-size: 13px; }
</style>
</head>
<body>

<section class="card card--contact">
  <div class="brand-first">Haul</div>
  <div class="brand-main">CRESTMARK</div>
  <div class="brand-rule"></div>
  <div class="tagline">Manufacture Certified / Nationally Certified</div>

  <div class="contact contact--phone">404-555-0148</div>
  <div class="contact contact--web">www.crestmarkhaul-example.com</div>
  <div class="contact contact--address">4812 Willowmere Lane, NE Ste: 210, Atlanta, GA 30399</div>

  <svg class="badge" viewBox="0 0 66 78" role="img" aria-label="Federal Competence Badge">
    <path d="M4 10 Q33 -2 62 10 L62 44 Q58 66 33 76 Q8 66 4 44 Z" fill="var(--white)" stroke="var(--gold)" stroke-width="4"/>
  </svg>

  <div class="maker-strip">
    <div class="maker"><span class="maker-dot"></span>RQT</div>
    <div class="maker"><span class="maker-dot"></span>ELVO</div>
    <div class="maker"><span class="maker-dot"></span>PUKA</div>
    <div class="maker"><span class="maker-dot"></span>Felinor</div>
    <div class="maker"><span class="maker-dot"></span>Tavrine</div>
    <div class="maker"><span class="maker-dot"></span>Tridessa</div>
    <div class="maker"><span class="maker-dot"></span>Brakewell</div>
    <div class="maker"><span class="maker-dot"></span>Stonevale</div>
    <div class="maker"><span class="maker-dot"></span>Valdora Kent</div>
  </div>
</section>

<section class="card card--brand">
  <div class="brand-band"></div>
  <div class="brand-first">Haul</div>
  <div class="brand-main">CRESTMARK</div>
  <div class="brand-rule"></div>
  <div class="tagline">Manufacture Certified / Nationally Certified</div>
</section>

</body>
</html>
```